Tolbek cards

I want a simple business card that pops.
Logo on one side.
On side two i want.
"Are you thinking about a new building on your property, or renovating an existing structure? Contact".....
Owners Name: Dale Whitacre
Owners Phone number: 610-555-0187
Address:4076 Copper Ridge RD, Ashcombe, PA 16832
Committed to Quality, Service, and Integrity

```html
<!DOCTYPE html>
<html lang="en">
<head>
<meta charset="utf-8">
<title>Tolbek Builders LLC – Business Card</title>
<link href="https://fonts.googleapis.com/css2?family=Montserrat:wght@400;500;600;800&display=swap" rel="stylesheet">
<style>
  :root {
    --backdrop: #979797;
    --card: #ffffff;
    --brown-dark: #432d1c;
    --brown-name: #5c3d26;
    --ink: #2b2522;
    --band-text: #ffffff;
  }
  * { margin: 0; padding: 0; box-sizing: border-box; }
  html, body {
    width: 1200px; height: 1108px; overflow: hidden;
    background: var(--backdrop);
    font-family: "Montserrat", Arial, sans-serif;
  }
  .canvas { position: relative; width: 1200px; height: 1108px; }
  .card {
    position: absolute; left: 242px; width: 715px; height: 408px;
    background: var(--card); border-radius: 27px; overflow: hidden;
  }
  .card--front { top: 119px; }
  .card--back { top: 580px; }

  .wordmark { position: absolute; text-align: center; color: var(--brown-dark); font-weight: 800; line-height: 1; }
  .wordmark__name { display: block; letter-spacing: -1px; }
  .wordmark__sub { display: block; letter-spacing: 1.5px; }

  .card--front .wordmark { left: 0; right: 0; top: 150px; }
  .card--front .wordmark__name { font-size: 92px; }
  .card--front .wordmark__sub { font-size: 27px; margin-top: 14px; }

  .card--back .wordmark { left: 40px; width: 320px; top: 176px; }
  .card--back .wordmark__name { font-size: 66px; }
  .card--back .wordmark__sub { font-size: 20px; margin-top: 9px; }

  .pitch {
    position: absolute; top: 19px; left: 0; right: 0; text-align: center;
    font-size: 17.5px; line-height: 28.5px; color: var(--ink); letter-spacing: 0.4px;
  }
  .divider { position: absolute; left: 366px; top: 94px; width: 2px; height: 220px; background: var(--brown-dark); }

  .contact { position: absolute; left: 395px; top: 88px; color: var(--ink); }
  .contact__name { font-size: 31px; font-weight: 600; color: var(--brown-name); line-height: 38px; }
  .contact__role { font-size: 17.5px; margin-top: 2px; letter-spacing: 0.4px; }
  .contact__address { font-size: 18px; line-height: 28.5px; margin-top: 19px; letter-spacing: 0.4px; }
  .contact__lines { list-style: none; margin-top: 12px; }
  .contact__lines li { display: flex; align-items: center; font-size: 18px; line-height: 28.5px; letter-spacing: 0.4px; }
  .contact__lines svg { width: 15px; height: 15px; margin-right: 10px; fill: var(--ink); }

  .tagline-band {
    position: absolute; left: 0; right: 0; top: 358px; height: 25px;
    background: var(--brown-dark); color: var(--band-text);
    font-size: 17px; line-height: 25px; text-align: center; letter-spacing: 0.5px;
  }
</style>
</head>
<body>
<div class="canvas">

  <section class="card card--front">
    <div class="wordmark">
      <span class="wordmark__name">TOLBEK</span>
      <span class="wordmark__sub">BUILDERS LLC</span>
    </div>
  </section>

  <section class="card card--back">
    <p class="pitch">Are you thinking about a new building on your<br>property, or renovating an existing structure? Contact</p>

    <div class="wordmark">
      <span class="wordmark__name">TOLBEK</span>
      <span class="wordmark__sub">BUILDERS LLC</span>
    </div>

    <div class="divider"></div>

    <div class="contact">
      <h1 class="contact__name">Dale Whitacre</h1>
      <p class="contact__role">Owner</p>
      <p class="contact__address">4076 Copper Ridge RD,<br>Ashcombe, PA 16832</p>
      <ul class="contact__lines">
        <li>
          <svg viewBox="0 0 16 16" aria-hidden="true"><path d="M1 6c0-2 3-3 7-3s7 1 7 3v1.5h-3.5V6c-1-.4-2.2-.6-3.5-.6S5.5 5.6 4.5 6v1.5H1z"/><path d="M3.5 8.5h9l1.5 5.5H2z"/></svg>
          610-555-0187
        </li>
        <li>
          <svg viewBox="0 0 16 16" aria-hidden="true"><path d="M1 3h14v1.2L8 9 1 4.2z"/><path d="M1 5.6l7 4.8 7-4.8V13H1z"/></svg>
          info@tolbek.buildersllc
        </li>
        <li>
          <svg viewBox="0 0 16 16" aria-hidden="true"><path d="M8 1a7 7 0 1 0 0 14A7 7 0 0 0 8 1zm0 1.6c.9 0 1.9 1.6 2.2 4.4H5.8C6.1 4.2 7.1 2.6 8 2.6zM2.7 8.6h1.9c.1 1.7.4 3.1 1 4.1A5.4 5.4 0 0 1 2.7 8.6zm0-1.2a5.4 5.4 0 0 1 2.9-4.1c-.6 1-.9 2.4-1 4.1zm5.3 6c-.9 0-1.9-1.6-2.2-4.8h4.4c-.3 3.2-1.300 4.8-2.2 4.8zm2.4-.7c.6-1 .9-2.4 1-4.1h1.9a5.4 5.4 0 0 1-2.9 4.1zm1-5.3c-.1-1.7-.4-3.1-1-4.1a5.4 5.4 0 0 1 2.9 4.1z"/></svg>
          www.tolbek.buildersllc
        </li>
      </ul>
    </div>

    <div class="tagline-band">Committed to Quality, Service, and Integrity</div>
  </section>

</div>
</body>
</html>
```